Website design for a new product

I would like a sccial media style and interactive site
The product is a phone case with a selfie stick built in. So posting selfies on the site would be great
I would need a landing page , a product page and a promo /selfie page
Below is the FB page and the current shopify shop
I have bought the domain name purchased
https://pocketlume.examplestore.com
https://www.examplesocial.com/brightgripwandcase/posts/918273645501928:0

Target Market(s)

Teens 13 - 19

Industry/Entity Type

Media

Number of Pages Required

3 page

Font styles to use
Other font styles liked:
• Black out is the logo

Colors

Designer to choose colors to be used in the design.

Requirements
Must have
• I'm open to anything

```html
<!DOCTYPE html>
<html lang="en">
<head>
<meta charset="utf-8">
<title>Pocketlume</title>
<link rel="stylesheet" href="https://fonts.googleapis.com/css2?family=Roboto:wght@400;500;700&family=Open+Sans:wght@400;600;700&display=swap">
<style>
:root{
  --black:#0b0b0b;
  --ink:#333;
  --muted:#6d6d6d;
  --navy:#1b3a5c;
  --blue:#1f6fb2;
  --btn:#15345a;
  --line:#e3e3e3;
  --white:#fff;
  --icon:#8a8a8a;
}
*{margin:0;padding:0;box-sizing:border-box}
html,body{width:1200px;height:2356px;overflow:hidden;background:var(--white)}
body{position:relative;font-family:"Open Sans",Arial,sans-serif;color:var(--ink)}
h1,h2,h3,h4{font-weight:400}

/* header */
.site-header{position:absolute;left:0;top:0;width:1200px;height:97px;background:var(--black)}
.brand{position:absolute;left:86px;top:31px;font-family:"Roboto",sans-serif;font-weight:400;font-size:25px;letter-spacing:5px;color:var(--white)}
.main-nav a{position:absolute;top:41px;font-family:"Roboto",sans-serif;font-weight:500;font-size:12px;color:var(--white);text-decoration:none}
.nav-btn{position:absolute;top:23px;width:50px;height:50px;border:1.5px solid #777;border-radius:50%}
.nav-btn svg{position:absolute;left:17px;top:17px}

/* hero */
.hero{position:absolute;left:0;top:97px;width:1200px;height:534px;background:linear-gradient(90deg,#ece9ee 0%,#f5f4f6 60%,#eceaed 100%)}
.hero-photo{position:absolute;left:0;top:0;width:590px;height:534px;background:linear-gradient(100deg,#e9e6ea 0%,#d8c6bc 25%,#7a625a 50%,#3b3136 70%,#e9e7ea 100%)}
.hero-tag{position:absolute;left:741px;top:242px;height:38px;padding:0 8px;background:#000;color:#fff;font-family:"Roboto",sans-serif;font-size:24px;letter-spacing:4px;line-height:38px}
.hero-text{position:absolute;left:739px;top:306px;width:380px;font-size:11.5px;line-height:27px;color:var(--muted)}
.btn-outline{position:absolute;left:740px;top:410px;width:138px;height:46px;border:1px solid #9a9a9a;font-family:"Roboto",sans-serif;font-size:17px;color:#555;text-align:center;line-height:44px;background:rgba(255,255,255,.3)}
.dots span{position:absolute;top:507px;width:13px;height:13px;border:1.5px solid #8a8a8a;border-radius:50%}
.dots span.on{border-color:var(--blue)}

/* sections */
.section-title{position:absolute;left:0;width:1200px;text-align:center;font-family:"Roboto",sans-serif;font-weight:400;font-size:27px;color:var(--navy)}
.section-sub{position:absolute;left:0;width:1200px;text-align:center;font-size:11px;color:var(--muted)}

.product{position:absolute;top:771px;width:246px;height:329px;border:1px solid var(--line);text-align:center}
.product-img{position:absolute;left:24px;top:18px;width:198px;height:160px;border-radius:6px}
.price{position:absolute;left:0;top:202px;width:100%;font-family:"Roboto",sans-serif;font-weight:500;font-size:19px;color:var(--blue)}
.product-name{position:absolute;left:0;top:237px;width:100%;font-family:"Roboto",sans-serif;font-size:16.5px;color:#333}
.actions{position:absolute;left:63px;top:273px;width:120px;height:32px}
.actions span{position:absolute;top:0;width:32px;height:32px;border:1px solid #bbb;border-radius:50%}
.actions svg{position:absolute;left:9px;top:9px}
.divider{position:absolute;left:86px;top:1156px;width:1028px;height:1px;background:var(--line)}

.post{position:absolute;top:1286px;width:325px}
.post-img{width:325px;height:206px}
.post-title{margin-top:30px;font-family:"Roboto",sans-serif;font-weight:500;font-size:14px;color:#222}
.post-meta{margin-top:14px;height:38px;border-top:1px solid var(--line);border-bottom:1px solid var(--line);font-size:9px;color:#888;position:relative}
.post-meta span{position:absolute;top:13px;display:flex;align-items:center;gap:5px}
.post-text{margin-top:17px;font-size:11.5px;line-height:23px;color:#555}

/* about */
.about{position:absolute;left:0;top:1725px;width:1200px;height:416px;background:linear-gradient(90deg,#f2f4f7 0%,#e9edf2 50%,#eef1f5 100%)}
.about-title{position:absolute;left:86px;top:40px;font-family:"Roboto",sans-serif;font-weight:400;font-size:27px;color:var(--navy)}
.about-text{position:absolute;left:86px;top:92px;width:430px;font-size:11.5px;line-height:23px;color:#555}
.checks{position:absolute;left:86px;top:188px;list-style:none}
.checks li{position:relative;height:33px;padding-left:31px;font-size:11.5px;color:#666}
.checks svg{position:absolute;left:0;top:3px}
.btn-solid{position:absolute;left:86px;top:334px;width:126px;height:41px;background:var(--btn);color:#fff;font-family:"Roboto",sans-serif;font-weight:500;font-size:14px;text-align:center;line-height:41px}
.about-photo{position:absolute;left:565px;top:20px;width:555px;height:385px;border-radius:4px;background:linear-gradient(160deg,#e4e8ee 0%,#cfd4dc 35%,#9aa2b0 55%,#dfe3e9 80%,#eef1f5 100%)}

/* footer */
.site-footer{position:absolute;left:0;top:2141px;width:1200px;height:215px;background:#111}
.foot-h{position:absolute;top:33px;font-family:"Roboto",sans-serif;font-weight:500;font-size:14px;color:#fff}
.foot-t{position:absolute;font-size:11.5px;line-height:19px;color:#ddd}
.email{position:absolute;left:624px;top:64px;width:210px;height:40px;background:#fff;font-size:11px;color:#999;padding:12px 12px}
.subscribe{position:absolute;left:843px;top:64px;width:90px;height:40px;background:var(--blue);color:#fff;font-size:11px;font-weight:700;text-align:center;line-height:38px;border:1px solid #5a9fd8}
.social span{position:absolute;top:72px;width:32px;height:32px;border:2px solid #fff;border-radius:50%}
.social svg{position:absolute;left:7px;top:7px}
.copyright{position:absolute;left:0;top:176px;width:1200px;text-align:center;font-size:11.5px;color:#eee}
</style>
</head>
<body>

<header class="site-header">
  <div class="brand">POCKETLUME</div>
  <nav class="main-nav">
    <a style="left:627px">HOME</a>
    <a style="left:713px">ABOUT US</a>
    <a style="left:820px">CATALOG</a>
    <a style="left:924px">CONTACT US</a>
  </nav>
  <div class="nav-btn" style="left:1005px"><svg width="14" height="14" viewBox="0 0 14 14"><circle cx="6" cy="6" r="4" fill="none" stroke="#fff" stroke-width="1.6"/><line x1="9" y1="9" x2="12" y2="12" stroke="#fff" stroke-width="1.8"/></svg></div>
  <div class="nav-btn" style="left:1065px"><svg width="14" height="14" viewBox="0 0 14 14"><path d="M1 2h2l2 7h6l1.5-5H4" fill="none" stroke="#fff" stroke-width="1.5"/><circle cx="6" cy="12" r="1.2" fill="#fff"/><circle cx="10" cy="12" r="1.2" fill="#fff"/></svg></div>
</header>

<section class="hero">
  <div class="hero-photo" role="img" aria-label="Two friends taking a selfie with a phone on a selfie stick while holding tea cups"></div>
  <div class="hero-tag">POCKETLUME</div>
  <p class="hero-text">Sed ut perspiciatis unde omnis iste natus error sit voluptatem accus-antium doloremque laudantium, totam rem aperiam, eaque ipsa qua quasi architecto beatae vitae dicta sunt explicabo</p>
  <div class="btn-outline">READ MORE</div>
  <div class="dots"><span style="left:1063px"></span><span class="on" style="left:1081px"></span><span style="left:1099px"></span></div>
</section>

<h2 class="section-title" style="top:671px">OUR PRODUCTS</h2>
<p class="section-sub" style="top:719px">Sed ut perspiciatis unde omnis iste natus error sit voluptatem accusantium doloremque laudantium, totam rem aperiam</p>

<div class="product" style="left:86px">
  <div class="product-img" role="img" aria-label="Black phone case with extended selfie stick" style="background:linear-gradient(150deg,#fff 0%,#fff 20%,#2a2a2a 45%,#c9c9c9 60%,#fff 90%)"></div>
  <div class="price">$ 29.95</div><div class="product-name">THE PHONE CASE</div>
  <div class="actions">
    <span style="left:0"><svg width="13" height="13" viewBox="0 0 14 14"><path d="M1 2h2l2 7h6l1.5-5H4" fill="none" stroke="#8a8a8a" stroke-width="1.4"/><circle cx="6" cy="12" r="1.1" fill="#8a8a8a"/><circle cx="10" cy="12" r="1.1" fill="#8a8a8a"/></svg></span>
    <span style="left:41px"><svg width="13" height="13" viewBox="0 0 14 14"><path d="M7 12L2 7a2.8 2.8 0 0 1 5-3.5A2.8 2.8 0 0 1 12 7z" fill="none" stroke="#8a8a8a" stroke-width="1.4"/></svg></span>
    <span style="left:82px"><svg width="13" height="13" viewBox="0 0 14 14"><path d="M1 4h11M9 1l3 3-3 3M13 10H2M5 7l-3 3 3 3" fill="none" stroke="#8a8a8a" stroke-width="1.3"/></svg></span>
  </div>
</div>
<div class="product" style="left:346px">
  <div class="product-img" role="img" aria-label="Phone cases in pink, blue, purple and black" style="background:linear-gradient(90deg,#fff 0%,#f2d3dc 20%,#c9ccd6 40%,#3f4a7a 55%,#d8d8d8 70%,#2b2b2b 82%,#fff 100%)"></div>
  <div class="price">$ 29.95</div><div class="product-name">MULTIPLE COLOURS</div>
  <div class="actions">
    <span style="left:0"><svg width="13" height="13" viewBox="0 0 14 14"><path d="M1 2h2l2 7h6l1.5-5H4" fill="none" stroke="#8a8a8a" stroke-width="1.4"/><circle cx="6" cy="12" r="1.1" fill="#8a8a8a"/><circle cx="10" cy="12" r="1.1" fill="#8a8a8a"/></svg></span>
    <span style="left:41px"><svg width="13" height="13" viewBox="0 0 14 14"><path d="M7 12L2 7a2.8 2.8 0 0 1 5-3.5A2.8 2.8 0 0 1 12 7z" fill="none" stroke="#8a8a8a" stroke-width="1.4"/></svg></span>
    <span style="left:82px"><svg width="13" height="13" viewBox="0 0 14 14"><path d="M1 4h11M9 1l3 3-3 3M13 10H2M5 7l-3 3 3 3" fill="none" stroke="#8a8a8a" stroke-width="1.3"/></svg></span>
  </div>
</div>
<div class="product" style="left:606px">
  <div class="product-img" role="img" aria-label="Navy phone case with built in selfie stick" style="background:linear-gradient(160deg,#fff 0%,#2c3a6b 22%,#e4e6ec 45%,#c5c8d2 70%,#fff 100%)"></div>
  <div class="price">$ 29.95</div><div class="product-name">BUILT IN SELFIE STICK</div>
  <div class="actions">
    <span style="left:0"><svg width="13" height="13" viewBox="0 0 14 14"><path d="M1 2h2l2 7h6l1.5-5H4" fill="none" stroke="#8a8a8a" stroke-width="1.4"/><circle cx="6" cy="12" r="1.1" fill="#8a8a8a"/><circle cx="10" cy="12" r="1.1" fill="#8a8a8a"/></svg></span>
    <span style="left:41px"><svg width="13" height="13" viewBox="0 0 14 14"><path d="M7 12L2 7a2.8 2.8 0 0 1 5-3.5A2.8 2.8 0 0 1 12 7z" fill="none" stroke="#8a8a8a" stroke-width="1.4"/></svg></span>
    <span style="left:82px"><svg width="13" height="13" viewBox="0 0 14 14"><path d="M1 4h11M9 1l3 3-3 3M13 10H2M5 7l-3 3 3 3" fill="none" stroke="#8a8a8a" stroke-width="1.3"/></svg></span>
  </div>
</div>
<div class="product" style="left:866px">
  <div class="product-img" role="img" aria-label="Front and back of a phone in its case" style="background:linear-gradient(90deg,#fff 0%,#222 18%,#b8a4a0 30%,#222 45%,#222 55%,#cfcfcf 68%,#222 82%,#fff 100%)"></div>
  <div class="price">$ 29.95</div><div class="product-name">RANGE OF 4 DIFFERENT</div>
  <div class="actions">
    <span style="left:0"><svg width="13" height="13" viewBox="0 0 14 14"><path d="M1 2h2l2 7h6l1.5-5H4" fill="none" stroke="#8a8a8a" stroke-width="1.4"/><circle cx="6" cy="12" r="1.1" fill="#8a8a8a"/><circle cx="10" cy="12" r="1.1" fill="#8a8a8a"/></svg></span>
    <span style="left:41px"><svg width="13" height="13" viewBox="0 0 14 14"><path d="M7 12L2 7a2.8 2.8 0 0 1 5-3.5A2.8 2.8 0 0 1 12 7z" fill="none" stroke="#8a8a8a" stroke-width="1.4"/></svg></span>
    <span style="left:82px"><svg width="13" height="13" viewBox="0 0 14 14"><path d="M1 4h11M9 1l3 3-3 3M13 10H2M5 7l-3 3 3 3" fill="none" stroke="#8a8a8a" stroke-width="1.3"/></svg></span>
  </div>
</div>

<div class="divider"></div>

<h2 class="section-title" style="top:1189px">LATEST BLOG</h2>
<p class="section-sub" style="top:1236px">Sed ut perspiciatis unde omnis iste natus error sit voluptatem accusantium doloremque laudantium, totam rem aperiam</p>

<article class="post" style="left:86px">
  <div class="post-img" role="img" aria-label="Man taking a selfie by a canal" style="background:linear-gradient(160deg,#9fb3c6 0%,#7b6e73 50%,#4e5d63 100%)"></div>
  <h3 class="post-title">SED UT PERSPICIATIS..</h3>
  <div class="post-meta"><span style="left:0">◷ 27 JUNE 2017</span><span style="left:110px">▭ 120</span><span style="left:188px">▴ LIKE</span><span style="left:258px">↗ SHARE</span></div>
  <p class="post-text">Sed ut perspiciatis unde omnis iste natus error sit volupta-tem accusantium doloremque laudantium, totam rem ape architecto beatae vitae dicta sunt explicabo.</p>
</article>
<article class="post" style="left:437px">
  <div class="post-img" role="img" aria-label="Phone held on a selfie stick against a blurred background" style="background:linear-gradient(150deg,#2e3520 0%,#8c8b55 45%,#c9b795 100%)"></div>
  <h3 class="post-title">SED UT PERSPICIATIS..</h3>
  <div class="post-meta"><span style="left:0">◷ 27 JUNE 2017</span><span style="left:110px">▭ 120</span><span style="left:188px">▴ LIKE</span><span style="left:258px">↗ SHARE</span></div>
  <p class="post-text">Sed ut perspiciatis unde omnis iste natus error sit volupta-tem accusantium doloremque laudantium, totam rem ape architecto beatae vitae dicta sunt explicabo.</p>
</article>
<article class="post" style="left:788px">
  <div class="post-img" role="img" aria-label="Selfie stick above a city skyline by the sea" style="background:linear-gradient(180deg,#bcd3e8 0%,#dfe7ee 50%,#c79a78 75%,#6f8aa0 100%)"></div>
  <h3 class="post-title">SED UT PERSPICIATIS..</h3>
  <div class="post-meta"><span style="left:0">◷ 27 JUNE 2017</span><span style="left:110px">▭ 120</span><span style="left:188px">▴ LIKE</span><span style="left:258px">↗ SHARE</span></div>
  <p class="post-text">Sed ut perspiciatis unde omnis iste natus error sit volupta-tem accusantium doloremque laudantium, totam rem ape architecto beatae vitae dicta sunt explicabo.</p>
</article>

<section class="about">
  <h2 class="about-title">ABOUT US</h2>
  <p class="about-text">Sed ut perspiciatis unde omnis iste natus error sit voluptatem accusantium dolo-rem que laudantium, totam rem aperiam, eaque ipsa quae ab illo inventore veri-tatis et quasi architecto beatae vitae dicta sunt explicabo.</p>
  <ul class="checks">
    <li><svg width="12" height="10" viewBox="0 0 12 10"><path d="M1 5l3.5 3.5L11 1" fill="none" stroke="#15345a" stroke-width="2.2"/></svg>Sed ut perspiciatis unde omnis iste natus error</li>
    <li><svg width="12" height="10" viewBox="0 0 12 10"><path d="M1 5l3.5 3.5L11 1" fill="none" stroke="#15345a" stroke-width="2.2"/></svg>Sit voluptatem accusantium dolorem que laudantium,</li>
    <li><svg width="12" height="10" viewBox="0 0 12 10"><path d="M1 5l3.5 3.5L11 1" fill="none" stroke="#15345a" stroke-width="2.2"/></svg>Totam rem aperiam, eaque ipsa quae ab illo</li>
    <li><svg width="12" height="10" viewBox="0 0 12 10"><path d="M1 5l3.5 3.5L11 1" fill="none" stroke="#15345a" stroke-width="2.2"/></svg>Inventore veritatis et quasi architecto</li>
  </ul>
  <div class="btn-solid">READ MORE</div>
  <div class="about-photo" role="img" aria-label="Phone case with its selfie stick extended beside a second navy case"></div>
</section>

<footer class="site-footer">
  <h4 class="foot-h" style="left:97px">CONTACT US</h4>
  <p class="foot-t" style="left:97px;top:68px">#1245 Lorem Ipsum dummy Text<br>text Lorem Ipsum</p>
  <p class="foot-t" style="left:346px;top:68px">+(000)-121-1231<br>info@pocketlume.examplestore.com/</p>
  <h4 class="foot-h" style="left:624px">JOIN OUR MAILING LIST</h4>
  <div class="email">Email:</div>
  <div class="subscribe">SUBSCRIBE</div>
  <h4 class="foot-h" style="left:991px">FOLLOW US</h4>
  <div class="social">
    <span style="left:991px"><svg width="14" height="14" viewBox="0 0 14 14"><circle cx="3" cy="7" r="2" fill="#fff"/><circle cx="11" cy="3" r="2" fill="#fff"/><circle cx="11" cy="11" r="2" fill="#fff"/><path d="M3 7L11 3M3 7l8 4" stroke="#fff" stroke-width="1.2"/></svg></span>
    <span style="left:1029px"><svg width="14" height="14" viewBox="0 0 14 14"><circle cx="3" cy="7" r="2" fill="#fff"/><circle cx="11" cy="3" r="2" fill="#fff"/><circle cx="11" cy="11" r="2" fill="#fff"/><path d="M3 7L11 3M3 7l8 4" stroke="#fff" stroke-width="1.2"/></svg></span>
    <span style="left:1067px"><svg width="14" height="14" viewBox="0 0 14 14"><circle cx="3" cy="7" r="2" fill="#fff"/><circle cx="11" cy="3" r="2" fill="#fff"/><circle cx="11" cy="11" r="2" fill="#fff"/><path d="M3 7L11 3M3 7l8 4" stroke="#fff" stroke-width="1.2"/></svg></span>
  </div>
  <p class="copyright">Copyright © 2017 Pocketlume.All rights are reserved</p>
</footer>

</body>
</html>
```